Our companies name is The Gilded Ladle and we specialize in craft cupcakes, what I mean by that is that we bake our cupcakes with craft beer and other alcoholic drinks. We are trying to focus on being elegant but at the same time unpretentious. Since we are incorporating beer in our cupcakes we want the business card to have our logo in the front and our information in the back.

Once we select the best design we will provide the contact information to be added. Thank you.

Industry/Entity Type

Business

Font styles to use
Decorative
Script

Requirements
Must have
• Round corners
Should not have
• Square corners

```html
<!DOCTYPE html>
<html lang="en">
<head>
<meta charset="utf-8">
<title>The Gilded Ladle – Business Cards</title>
<link rel="stylesheet" href="https://fonts.googleapis.com/css2?family=Rye&family=Arimo:wght@400&display=swap">
<style>
  :root {
    --backdrop: #eee8e1;
    --card: #ffffff;
    --ink: #151515;
    --band: #111212;
    --accent-red: #e63b4b;
    --rule: #9a9a9a;
    --shadow: rgba(60, 35, 20, 0.25);
  }
  * { margin: 0; padding: 0; box-sizing: border-box; }
  html, body {
    width: 1200px;
    height: 914px;
    overflow: hidden;
    background: var(--backdrop);
  }
  .canvas {
    position: relative;
    width: 1200px;
    height: 914px;
  }
  .card {
    position: absolute;
    width: 540px;
    height: 310px;
    background: var(--card);
    border-radius: 18px;
    overflow: hidden;
    box-shadow: 0 10px 28px var(--shadow);
  }
  /* Back of card: brand + website */
  .card--back { left: 600px; top: 90px; }
  .card--back .brand {
    position: absolute;
    left: 0; right: 0; top: 110px;
    display: flex;
    justify-content: center;
    align-items: center;
    gap: 14px;
  }
  .card--back .website {
    position: absolute;
    left: 0; right: 0; top: 212px;
    text-align: center;
    font-family: "Rye", serif;
    font-size: 15px;
    letter-spacing: 0.5px;
    color: var(--accent-red);
  }
  .brand-dot {
    width: 26px; height: 26px;
    border-radius: 50%;
    background: var(--band);
    flex: none;
  }
  .brand-name {
    font-family: "Rye", serif;
    font-size: 30px;
    color: var(--accent-red);
    white-space: nowrap;
  }
  /* Front of card: details */
  .card--front { left: 60px; top: 500px; }
  .card--front .brand {
    position: absolute;
    left: 22px; top: 100px;
    width: 220px;
    display: flex;
    align-items: center;
    gap: 10px;
  }
  .card--front .brand-name { font-size: 22px; }
  .card--front .brand-dot { width: 20px; height: 20px; }
  .divider {
    position: absolute;
    left: 262px; top: 30px;
    width: 1px; height: 190px;
    background: var(--rule);
  }
  .details {
    position: absolute;
    left: 290px; top: 62px;
    font-family: "Arimo", sans-serif;
    color: var(--ink);
  }
  .person-name {
    font-family: "Rye", serif;
    font-size: 20px;
    color: var(--accent-red);
    letter-spacing: 0.5px;
  }
  .person-role { font-size: 13px; margin-top: 2px; }
  .contact-list { list-style: none; margin-top: 22px; }
  .contact-list li {
    display: flex;
    align-items: center;
    gap: 12px;
    font-size: 16px;
    line-height: 24px;
  }
  .contact-list svg { width: 14px; height: 14px; flex: none; fill: var(--accent-red); }
  .address-band {
    position: absolute;
    left: 0; right: 0; bottom: 0;
    height: 56px;
    background: var(--band);
    display: flex;
    align-items: center;
    gap: 16px;
    padding-left: 40px;
    font-family: "Arimo", sans-serif;
    font-size: 15px;
    color: var(--accent-red);
  }
  .address-band svg { width: 14px; height: 18px; flex: none; }
</style>
</head>
<body>
<main class="canvas">

  <section class="card card--back" aria-label="Card back">
    <div class="brand">
      <span class="brand-dot"></span>
      <span class="brand-name">The Gilded Ladle</span>
    </div>
    <p class="website">WWW.GILDEDLADLE.COM</p>
  </section>

  <section class="card card--front" aria-label="Card front">
    <div class="brand">
      <span class="brand-dot"></span>
      <span class="brand-name">The Gilded Ladle</span>
    </div>
    <div class="divider"></div>
    <div class="details">
      <h1 class="person-name">EMPLOYEE NAME</h1>
      <p class="person-role">Managing Director</p>
      <ul class="contact-list">
        <li>
          <svg viewBox="0 0 16 16" aria-hidden="true"><path d="M3 1h3l1.5 3.5-2 1.3a8 8 0 0 0 4.7 4.7l1.3-2L15 10v3a2 2 0 0 1-2 2A12 12 0 0 1 1 3a2 2 0 0 1 2-2z"/></svg>
          0098 7654 321
        </li>
        <li>
          <svg viewBox="0 0 16 16" aria-hidden="true"><path d="M1 3h14v10H1z M1 3l7 6 7-6" fill="none" stroke="#e63b4b" stroke-width="1.6"/></svg>
          hello@gildedladle.com
        </li>
        <li>
          <svg viewBox="0 0 16 16" aria-hidden="true"><circle cx="8" cy="8" r="6.5" fill="none" stroke="#e63b4b" stroke-width="1.5"/><path d="M1.5 8h13M8 1.5c3 3.5 3 9.5 0 13M8 1.5c-3 3.5-3 9.5 0 13" fill="none" stroke="#e63b4b" stroke-width="1.2"/></svg>
          www.gildedladle.com
        </li>
      </ul>
    </div>
    <div class="address-band">
      <svg viewBox="0 0 14 18" aria-hidden="true"><path d="M7 1a6 6 0 0 1 6 6c0 4-6 10-6 10S1 11 1 7a6 6 0 0 1 6-6z" fill="none" stroke="#ffffff" stroke-width="1.6"/></svg>
      <span>The Gilded Ladle 14 Maple Row, Fairhaven, NJ 00000</span>
    </div>
  </section>

</main>
</body>
</html>
```